Sleek wordpress site for Bramblecrest finishing works

We are a commercial job shop that serves B2B, govt & LEO and retail clients.We need a wordpress site with 6 individual pages: homepage, coating, laser engraving, laser cutting, part marking, and contact us. I have attached an outline of the desired flow and sub headings for each page. I would like to incorporate the colors of the logo through out the site to be clean and sleek enough to appeal to B2B commercial clients yet be inviting enough for retail clients.

I would like to have easy picture functionality so photographs on each page can be updated easily.

Target Market(s)

B2B industrial & Govt and Military part marking, laser engraving and coating: machine shops, aerospace companies, tool manufactures. Retail: personalized gifts, Job Shop

Coding

Coded - Design and coding required

Font styles to use
Sans Serif
Other font styles liked:
• Open to suggestion

Colors
0255a3
3176b5
eaf1f7
cfdeed
ffffff

Requirements
Must have
• Clean easy to navigate flow, separate pages as indicated on attached outline, high class feel. Great picture functionality, professional and inviting feel,
• **update: needs to be optimized for mobile, should have a gallery function. Gallery can be an additional page or embedded
Nice to have
• Social media connectivity links,
Should not have
• crappy plugins that make back-end management difficult, no blog

```html
<!DOCTYPE html>
<html lang="en">
<head>
<meta charset="utf-8">
<title>Bramblecrest Finishing Works</title>
<link rel="stylesheet" href="https://fonts.googleapis.com/css2?family=Questrial&family=Quicksand:wght@400;500;600;700&family=Tinos:wght@700&display=swap">
<style>
:root{
  --blue:#0255a3;
  --blue-mid:#3176b5;
  --blue-pale:#eaf1f7;
  --blue-soft:#cfdeed;
  --white:#ffffff;
  --ink:#555b63;
}
*{box-sizing:border-box;margin:0;padding:0}
html,body{width:1200px;height:2419px;overflow:hidden;background:var(--white)}
body{position:relative;font-family:"Quicksand",sans-serif;color:var(--ink)}
.abs{position:absolute}
a{color:inherit}

/* hero */
.hero-photo{left:0;top:0;width:1200px;height:730px;background:linear-gradient(160deg,#4d535c 0%,#6d737b 35%,#3c4149 70%,#2b2f35 100%)}
.hero-cut{left:0;top:0}
.topbar{left:0;top:0;width:1200px;height:52px;color:var(--white);font-size:16px;font-family:"Questrial",sans-serif}
.topbar .contact-item{position:absolute;top:15px;display:flex;align-items:center;gap:12px;white-space:nowrap}
.social-row{display:flex}
.social-row span{border:1.5px solid var(--white);border-radius:50%;display:flex;align-items:center;justify-content:center}
.social-row span::after{content:"";width:30%;height:30%;border-radius:50%;background:var(--white)}
.topbar .socials{position:absolute;left:824px;top:10px;gap:8px}
.topbar .socials span{width:30px;height:30px}
.topbar .login{position:absolute;left:986px;top:16px;font-size:15px;white-space:nowrap}

.navbar{left:77px;top:53px;width:1046px;height:124px;background:var(--white);box-shadow:0 2px 8px rgba(0,0,0,.15)}
.brand{position:absolute;left:22px;top:38px;width:200px;display:flex;align-items:center;gap:10px;font-family:"Questrial",sans-serif;font-size:16px;color:var(--blue);line-height:1.2;text-transform:uppercase}
.brand .dot{width:24px;height:24px;border-radius:50%;background:var(--blue);flex:none}
.menu-item{position:absolute;top:51px;font-family:"Questrial",sans-serif;font-size:18px;color:#6a6f75;white-space:nowrap}
.menu-item.active{color:var(--blue);font-weight:600}
.search{position:absolute;left:958px;top:51px}
.cart{position:absolute;left:1003px;top:51px}
.cart b{position:absolute;right:-10px;top:-12px;width:19px;height:19px;border-radius:50%;background:var(--blue);color:var(--white);font-size:11px;display:flex;align-items:center;justify-content:center}

.hero-title{left:80px;top:256px;font-family:"Questrial",sans-serif;font-size:49px;line-height:58px;color:var(--white);text-shadow:0 2px 4px rgba(0,0,0,.35);font-weight:700;white-space:nowrap}
.hero-text{left:80px;top:380px;width:520px;font-size:16px;line-height:25px;color:var(--white)}
.btn{display:flex;align-items:center;justify-content:center;background:var(--blue);color:var(--white);font-family:"Questrial",sans-serif;font-size:19px;text-transform:uppercase;white-space:nowrap}
.hero-btn{left:77px;top:476px;width:157px;height:51px}

/* contact form */
.form-shadow{left:735px;top:502px;width:335px;height:456px;background:var(--blue-mid)}
.form-card{left:724px;top:490px;width:336px;height:458px;background:var(--blue-soft)}
.form-card h3{position:absolute;left:0;top:32px;width:100%;text-align:center;font-family:"Questrial",sans-serif;font-size:27px;color:var(--blue);font-weight:700}
.field{position:absolute;left:21px;width:292px;background:var(--white);font-size:13px;color:#777;padding:16px 14px}
.form-btn{position:absolute;left:89px;top:365px;width:156px;height:51px}

/* about */
.about-title{left:80px;top:840px;font-family:"Tinos",serif;font-size:35px;color:var(--blue);display:flex;align-items:center;gap:20px}
.about-title i{display:block;width:85px;height:1.5px;background:#9aa4ad}
.about-text{left:79px;top:904px;width:580px;font-size:13.5px;line-height:25px}
.read-more{font-size:15px;color:var(--blue);text-decoration:underline;text-transform:uppercase;font-family:"Questrial",sans-serif}
.about-more{left:79px;top:999px}

/* services */
.services-photo{left:0;top:1084px;width:1200px;height:542px;background:linear-gradient(120deg,#2c2f33 0%,#3d4146 45%,#2a2c30 100%)}
.services-title{left:0;top:1142px;width:1200px;display:flex;justify-content:center;align-items:center;gap:22px;font-family:"Tinos",serif;font-size:34px;color:var(--white)}
.services-title i{display:block;width:84px;height:1.5px;background:rgba(255,255,255,.6)}
.service{top:1245px;width:260px;text-align:center;color:var(--white)}
.service svg{display:block;margin:0 auto}
.service h4{margin-top:26px;font-family:"Questrial",sans-serif;font-size:22px;font-weight:500;white-space:nowrap}
.service p{margin:14px auto 0;width:230px;font-size:13.5px;line-height:25px}
.service .read-more{display:inline-block;margin-top:12px;color:var(--white);font-size:14px}

/* intro */
.intro-title{left:80px;top:1684px;font-family:"Tinos",serif;font-size:35px;color:var(--blue);white-space:nowrap}
.intro-text{left:79px;top:1748px;width:550px;font-size:13.5px;line-height:25px}
.intro-btn{left:77px;top:1929px;width:157px;height:52px}
.video{left:686px;top:1689px;width:437px;height:292px;background:radial-gradient(circle at 45% 75%,#6a5a7a 0%,#2e2c4a 45%,#191a2a 100%)}
.play{position:absolute;left:172px;top:100px;width:88px;height:88px;border-radius:50%;background:rgba(255,255,255,.55);display:flex;align-items:center;justify-content:center}
.play span{width:60px;height:60px;border-radius:50%;background:var(--white);display:flex;align-items:center;justify-content:center}

/* footer */
.footer{left:0;top:2032px;width:1200px;height:325px;background:var(--blue);color:var(--white)}
.footer-brand{position:absolute;left:77px;top:92px;width:210px;font-family:"Questrial",sans-serif;font-size:21px;line-height:26px;text-transform:uppercase;text-align:center}
.footer-rule{position:absolute;left:77px;top:205px;width:210px;height:1.5px;background:rgba(255,255,255,.8)}
.footer-social{position:absolute;left:83px;top:221px;gap:12px}
.footer-social span{width:40px;height:40px}
.footer h5{position:absolute;top:52px;font-family:"Tinos",serif;font-size:19px}
.footer ul{position:absolute;top:110px;list-style:none;font-size:13.5px;line-height:25px}
.touch{position:absolute;left:616px;top:105px;font-size:13.5px;line-height:25px}
.touch .row{display:flex;gap:16px;margin-bottom:14px}
.touch .row svg{flex:none;margin-top:4px}
.newsletter{position:absolute;left:885px;top:105px;width:240px;font-size:13.5px;line-height:25px}
.email-box{position:absolute;left:884px;top:200px;width:239px;height:52px;background:var(--white);border:3px solid var(--blue-soft);font-size:14px;color:#333;font-weight:600;padding:14px 12px}
.email-box span{position:absolute;right:7px;top:6px;width:40px;height:34px;background:var(--blue-mid);display:flex;align-items:center;justify-content:center}
.copyright{left:0;top:2357px;width:1200px;height:62px;background:var(--blue-mid);color:var(--white);display:flex;align-items:center;justify-content:center;font-size:14px}
.copyright b{margin:0 4px;text-transform:uppercase}
</style>
</head>
<body>

<div class="abs hero-photo" role="img" aria-label="Photo of a laser cutting head working over a perforated metal sheet"></div>
<svg class="abs hero-cut" width="1200" height="790" viewBox="0 0 1200 790" aria-hidden="true">
  <polygon points="0,626 331,729 1200,532 1200,790 0,790" fill="#ffffff"/>
  <line x1="45" y1="757" x2="1200" y2="520" stroke="#d5dbe1" stroke-width="1.5"/>
  <polygon points="75,698 83,702 83,711 75,715 67,711 67,702" fill="var(--blue)"/>
  <polygon points="280,752 297,761 297,779 280,788 263,779 263,761" fill="var(--white)" stroke="#c9d2db"/>
  <polygon points="280,757 292,764 292,777 280,784 268,777 268,764" fill="var(--blue)"/>
  <polygon points="540,723 552,730 552,743 540,750 528,743 528,730" fill="var(--blue)"/>
</svg>

<header class="abs topbar">
  <div class="contact-item" style="left:77px">
    <svg width="20" height="20" viewBox="0 0 24 24" fill="#fff"><path d="M6.6 10.8a15.1 15.1 0 0 0 6.6 6.6l2.2-2.2c.3-.3.7-.4 1-.2 1.1.4 2.3.6 3.6.6.6 0 1 .4 1 1V20c0 .6-.4 1-1 1A17 17 0 0 1 3 4c0-.6.4-1 1-1h3.5c.6 0 1 .4 1 1 0 1.3.2 2.5.6 3.6.1.3 0 .7-.2 1z"/></svg>
    <span>555.014.2286</span>
  </div>
  <div class="contact-item" style="left:242px">
    <svg width="20" height="16" viewBox="0 0 24 18"><path d="M1 1h22v16H1z" fill="#fff"/><path d="M1 1l11 9 11-9" stroke="#555" stroke-width="1.5" fill="none"/></svg>
    <span>hello@bramblecrestworks.com</span>
  </div>
  <div class="socials social-row"><span></span><span></span><span></span><span></span></div>
  <div class="login">Login or Register</div>
</header>

<nav class="abs navbar">
  <div class="brand"><span class="dot"></span><span>Bramblecrest finishing works</span></div>
  <span class="menu-item active" style="left:260px">Home</span>
  <span class="menu-item" style="left:339px">Coating</span>
  <span class="menu-item" style="left:432px">Laser Engraving</span>
  <span class="menu-item" style="left:589px">Lesar Cutting</span>
  <span class="menu-item" style="left:723px">Part Marketing</span>
  <span class="menu-item" style="left:871px">Contact</span>
  <svg class="search" width="22" height="22" viewBox="0 0 24 24" fill="none" stroke="var(--blue)" stroke-width="2.2"><circle cx="10" cy="10" r="7"/><path d="M15 15l6 6"/></svg>
  <span class="cart">
    <svg width="22" height="20" viewBox="0 0 24 22" fill="var(--blue)"><path d="M2 7h20l-3 13H5z"/><path d="M7 7l5-6 5 6" stroke="var(--blue)" stroke-width="2" fill="none"/></svg>
    <b>0</b>
  </span>
</nav>

<h1 class="abs hero-title">BRAMBLECREST FINISHING<br>WORKS</h1>
<p class="abs hero-text">Lorem Ipsum is simply dummy text of the printing and typesetting industry. Lorem Ipsum has been the industry's standard dummy text ever since the 1500s.</p>
<div class="abs btn hero-btn">Contact Us</div>

<div class="abs form-shadow"></div>
<form class="abs form-card">
  <h3>CONTACT US</h3>
  <div class="field" style="top:84px;height:50px">Name :</div>
  <div class="field" style="top:146px;height:51px">Email :</div>
  <div class="field" style="top:208px;height:52px">Phone :</div>
  <div class="field" style="top:271px;height:83px">Message :</div>
  <div class="btn form-btn">Submit Now</div>
</form>

<h2 class="abs about-title">About Us <i></i></h2>
<p class="abs about-text">Lorem Ipsum is simply dummy text of the printing and typesetting industry. Lorem Ipsum has been the industry's standard dummy text ever since the 1500s, when an unknown printer took a galley of type and scrambled it to make a type specimen book.</p>
<a class="abs read-more about-more">Read More</a>

<div class="abs services-photo" role="img" aria-label="Dimmed workshop photo of a technician at a machine"></div>
<h2 class="abs services-title"><i></i>Our Services<i></i></h2>

<div class="abs service" style="left:67px">
  <svg width="114" height="128" viewBox="0 0 114 128" role="img" aria-label="Coating service icon"><polygon points="57,2 111,33 111,95 57,126 3,95 3,33" fill="none" stroke="#fff" stroke-width="1.5"/><polygon points="57,9 105,37 105,91 57,119 9,91 9,37" fill="var(--blue)"/></svg>
  <h4>Coating</h4>
  <p>Lorem Ipsum is simply dummy text of the printing and typesetting industry.</p>
  <a class="read-more">Read More</a>
</div>
<div class="abs service" style="left:335px">
  <svg width="114" height="128" viewBox="0 0 114 128" role="img" aria-label="Laser engraving service icon"><polygon points="57,2 111,33 111,95 57,126 3,95 3,33" fill="none" stroke="#fff" stroke-width="1.5"/><polygon points="57,9 105,37 105,91 57,119 9,91 9,37" fill="var(--blue)"/></svg>
  <h4>Laser Engraving</h4>
  <p>Lorem Ipsum is simply dummy text of the printing and typesetting industry.</p>
  <a class="read-more">Read More</a>
</div>
<div class="abs service" style="left:604px">
  <svg width="114" height="128" viewBox="0 0 114 128" role="img" aria-label="Laser cutting service icon"><polygon points="57,2 111,33 111,95 57,126 3,95 3,33" fill="none" stroke="#fff" stroke-width="1.5"/><polygon points="57,9 105,37 105,91 57,119 9,91 9,37" fill="var(--blue)"/></svg>
  <h4>Lesar Cutting</h4>
  <p>Lorem Ipsum is simply dummy text of the printing and typesetting industry.</p>
  <a class="read-more">Read More</a>
</div>
<div class="abs service" style="left:872px">
  <svg width="114" height="128" viewBox="0 0 114 128" role="img" aria-label="Part marking service icon"><polygon points="57,2 111,33 111,95 57,126 3,95 3,33" fill="none" stroke="#fff" stroke-width="1.5"/><polygon points="57,9 105,37 105,91 57,119 9,91 9,37" fill="var(--blue)"/></svg>
  <h4>Part Marketing</h4>
  <p>Lorem Ipsum is simply dummy text of the printing and typesetting industry.</p>
  <a class="read-more">Read More</a>
</div>

<h2 class="abs intro-title">Bramblecrest Finishing Works</h2>
<p class="abs intro-text">Lorem Ipsum is simply dummy text of the printing and typesetting industry. Lorem Ipsum has been the industry's standard dummy text ever since the 1500s, when an unknown printer took a galley of type and scrambled it to make a type specimen book. It has survived not only five centuries, but also the leap into electronic the to typesetting, remaining essentially unchanged. It was popularised in the 1960s with the release of Letraset sheets containing Lorem Ipsum passages.</p>
<div class="abs btn intro-btn">Submit Now</div>
<div class="abs video" role="img" aria-label="Video still of a laser cutter throwing sparks over metal">
  <div class="play"><span><svg width="22" height="26" viewBox="0 0 22 26"><polygon points="3,1 21,13 3,25" fill="var(--blue)"/></svg></span></div>
</div>

<footer class="abs footer">
  <div class="footer-brand">Bramblecrest finishing works</div>
  <div class="footer-rule"></div>
  <div class="footer-social social-row"><span></span><span></span><span></span><span></span></div>

  <h5 style="left:348px">Navigation</h5>
  <ul style="left:348px"><li>Home</li><li>Coating</li><li>Laser engraving</li><li>Laser Cutting</li><li>Part Marking</li><li>Contact Us</li></ul>

  <h5 style="left:616px">Get In Touch</h5>
  <div class="touch">
    <div class="row"><svg width="16" height="22" viewBox="0 0 16 22"><path d="M8 0a8 8 0 0 1 8 8c0 6-8 14-8 14S0 14 0 8a8 8 0 0 1 8-8z" fill="#fff"/><circle cx="8" cy="8" r="3" fill="var(--blue)"/></svg><span>123 Building Name, Street,<br>City, Country - Zip code</span></div>
    <div class="row"><svg width="20" height="20" viewBox="0 0 24 24" fill="#fff"><path d="M6.6 10.8a15.1 15.1 0 0 0 6.6 6.6l2.2-2.2c.3-.3.7-.4 1-.2 1.1.4 2.3.6 3.6.6.6 0 1 .4 1 1V20c0 .6-.4 1-1 1A17 17 0 0 1 3 4c0-.6.4-1 1-1h3.5c.6 0 1 .4 1 1 0 1.3.2 2.5.6 3.6.1.3 0 .7-.2 1z"/></svg><span>555.014.2286</span></div>
    <div class="row"><svg width="22" height="16" viewBox="0 0 24 18"><path d="M1 1h22v16H1z" fill="#fff"/><path d="M1 1l11 9 11-9" stroke="var(--blue)" stroke-width="1.5" fill="none"/></svg><span>hello@bramblecrestworks.com</span></div>
  </div>

  <h5 style="left:885px">Newsletter</h5>
  <p class="newsletter">Lorem Ipsum is simply dummy text of the printing and typesetting the industry. Lorem Ipsum has.</p>
  <div class="email-box">Email<span><svg width="20" height="15" viewBox="0 0 24 18"><path d="M1 1h22v16H1z" fill="#fff"/><path d="M1 1l11 9 11-9" stroke="var(--blue-mid)" stroke-width="1.5" fill="none"/></svg></span></div>
</footer>

<div class="abs copyright">Copyright &copy; <b>Bramblecrest finishing works</b> - 2018 . All Right Reserved</div>

</body>
</html>
```